BOLD & MINIMALIST DESIGN NEEDED

We want a very bold but minimalistic business card design that is impactful and utilizes both sides of the business card. Our current logo is included for your use.

We want bold fonts and good use of negative space. We don't want the logo to overpower the design.

Target Market(s)

Professionals who are building new commercial buildings.

Industry/Entity Type

Construction

Contact Information for Business Card

Name, Title, email, office phone, cell phone, website

Font styles to use
Serif
Sans Serif

Requirements
Must have
• Bold design!

```html
<!DOCTYPE html>
<html lang="en">
<head>
<meta charset="utf-8">
<title>Summitline Design + Build — Business Card</title>
<link href="https://fonts.googleapis.com/css2?family=Oswald:wght@600&family=Poppins:wght@400;500&display=swap" rel="stylesheet">
<style>
  :root {
    --backdrop: #262626;
    --card: #222222;
    --card-edge: #2c2c2c;
    --white: #f2f2f2;
    --grey: #cfcfcf;
    --green: #76b02c;
    --ink: #151515;
  }
  * { margin: 0; padding: 0; box-sizing: border-box; }
  html, body { width: 1200px; height: 576px; overflow: hidden; background: var(--backdrop); }
  .canvas { position: relative; width: 1200px; height: 576px; }
  .card {
    position: absolute; top: 138px; width: 484px; height: 294px;
    background: var(--card); border-radius: 10px; overflow: hidden;
    border: 1px solid var(--card-edge);
  }
  .card--front { left: 102px; }
  .card--back { left: 596px; width: 481px; }

  .brand { display: flex; align-items: center; gap: 12px; }
  .brand__mark { width: 16px; height: 16px; background: var(--green); flex: none; }
  .brand__name {
    font-family: "Oswald", sans-serif; font-weight: 600; color: var(--white);
    text-transform: uppercase; line-height: 1;
  }
  .brand__name span { display: block; }

  .card--front .brand {
    position: absolute; left: 0; right: 0; top: 104px; justify-content: center;
  }
  .card--front .brand__name { font-size: 40px; letter-spacing: 1px; text-align: center; }
  .card--front .brand__name span + span { font-size: 16px; letter-spacing: 7px; margin-top: 6px; }

  .card--back .brand { position: absolute; left: 25px; top: 36px; }
  .card--back .brand__name { font-size: 31px; letter-spacing: 1px; }
  .card--back .brand__name span + span { font-size: 13px; letter-spacing: 5.5px; margin-top: 4px; }

  .name-band {
    position: absolute; left: 0; top: 126px; width: 284px; height: 67px;
    background: var(--green); padding: 15px 0 0 25px;
    font-family: "Poppins", sans-serif; color: var(--ink);
  }
  .name-band__name { font-size: 20px; font-weight: 500; line-height: 1.1; }
  .name-band__title { font-size: 11px; margin-top: 2px; }

  .contact {
    position: absolute; left: 30px; top: 221px; list-style: none;
    font-family: "Poppins", sans-serif; font-size: 12px; color: var(--grey);
  }
  .contact li { display: flex; align-items: center; gap: 8px; height: 17px; }
  .contact svg { width: 10px; height: 10px; fill: var(--green); flex: none; }

  .accent-block {
    position: absolute; right: 0; top: 36px; width: 150px; height: 258px;
    background: linear-gradient(160deg, #e9e9e9 0 48%, var(--green) 48% 100%);
  }
</style>
</head>
<body>
<main class="canvas">
  <section class="card card--front" aria-label="Card front">
    <div class="brand">
      <div class="brand__mark"></div>
      <p class="brand__name"><span>Summitline</span><span>Design + Build</span></p>
    </div>
  </section>

  <section class="card card--back" aria-label="Card back">
    <div class="brand">
      <p class="brand__name"><span>Summitline</span><span>Design + Build</span></p>
    </div>
    <div class="accent-block" role="img" aria-label="Brand accent block"></div>
    <div class="name-band">
      <p class="name-band__name">Daniel Moreno</p>
      <p class="name-band__title">Director</p>
    </div>
    <ul class="contact">
      <li><svg viewBox="0 0 10 10"><path d="M1 2.5C1 1.5 2 1 3 1h4c1 0 2 .5 2 1.5V4H7V3H3v1H1z M2 5h6l1 4H1z"/></svg>555-014-0182</li>
      <li><svg viewBox="0 0 10 10"><path d="M0 2h10v6H0z" /><path d="M0 2l5 3.5L10 2" fill="none" stroke="#222" stroke-width="1"/></svg>daniel@summitline.com</li>
      <li><svg viewBox="0 0 10 10"><circle cx="5" cy="5" r="4.5"/><path d="M0.5 5h9M5 0.5v9" stroke="#222" stroke-width="0.8"/></svg>www.summitline.com</li>
    </ul>
  </section>
</main>
</body>
</html>
```